Brindle Asset Management Vendor Recruiting Email

We need a digital flyer to email and post on Social media to attract new vendors to our website to apply to complete maintenance work on our clients homes. I have one flyer we had produced recently that we are un-happy with. It is attached.

The example given is what we do not want!! We do not want any of the pictures used from the existing one

Target Market(s)

Construction companies and handyman

Industry/Entity Type

Residential maintenance and repairs

Requirements
Must have
• Join our team as the header not become a vendor

```html
<!DOCTYPE html>
<html lang="en">
<head>
<meta charset="utf-8">
<title>Brindle Asset Management – Join Our Team</title>
<link rel="stylesheet" href="https://fonts.googleapis.com/css2?family=Luckiest+Guy&family=Oswald:wght@600;700&family=Lexend:wght@500&family=Open+Sans:ital,wght@1,600&display=swap">
<style>
  :root {
    --purple: #674c7e;
    --purple-deep: #5a2a8a;
    --lime: #d4e21f;
    --white: #ffffff;
    --black: #050306;
    --lavender: #8a87c0;
    --blue: #1b74bb;
    --brand-bg: #0d0b18;
  }
  * { box-sizing: border-box; margin: 0; padding: 0; }
  html, body { width: 1200px; height: 1200px; overflow: hidden; background: var(--white); }
  .flyer {
    position: absolute; left: 50px; top: 108px; width: 1100px; height: 985px;
    background: var(--purple); font-family: "Lexend", sans-serif; color: var(--white);
  }
  .frame {
    position: absolute; left: 31px; top: 19px; width: 1039px; height: 948px;
    border: 2px solid var(--white); border-radius: 24px; overflow: hidden;
  }
  .headline {
    position: absolute; left: 0; right: 0; top: 55px; text-align: center;
    font-family: "Luckiest Guy", "Lilita One", sans-serif; font-weight: 400;
    font-size: 96px; line-height: 100px; letter-spacing: 1px;
  }
  .divider { position: absolute; left: 503px; top: 263px; width: 2px; height: 419px; background: var(--white); }
  .benefits { position: absolute; left: 60px; top: 0; width: 440px; list-style: none; }
  .benefits li, .requirements li {
    position: absolute; left: 0; padding-left: 30px; font-size: 23.5px; line-height: 31px; white-space: nowrap;
  }
  .benefits li::before, .requirements li::before {
    content: ""; position: absolute; left: 2px; top: 9px; width: 11px; height: 11px;
    border-radius: 50%; background: var(--lime);
  }
  .requirements { position: absolute; left: 537px; top: 0; width: 500px; list-style: none; }
  .requirements li { font-size: 21.5px; line-height: 28px; padding-left: 32px; }
  .requirements-title {
    position: absolute; left: 533px; top: 258px; width: 480px;
    font-family: "Oswald", sans-serif; font-weight: 700; font-size: 37px; line-height: 48px;
    color: var(--lime); transform: skewX(-4deg);
  }
  .contact-tab {
    position: absolute; left: 188px; top: 690px; width: 138px; height: 50px;
    background: var(--white); border-radius: 5px; transform: rotate(-4deg);
    font-family: "Oswald", sans-serif; font-weight: 700; font-size: 24px; color: var(--purple-deep);
    text-align: center; line-height: 36px;
  }
  .phone {
    position: absolute; left: 114px; top: 731px; width: 472px; height: 110px;
    background: var(--blue); border: 3px solid var(--white); border-radius: 6px;
    transform: rotate(-3deg); box-shadow: 2px 3px 4px rgba(0,0,0,.35);
    font-family: "Oswald", sans-serif; font-weight: 700; font-size: 76px; line-height: 100px;
    text-align: center; letter-spacing: 1px;
  }
  .footer-band { position: absolute; left: 0; top: 871px; width: 100%; height: 55px; background: var(--black); }
  .footer-accent { position: absolute; left: 0; top: 926px; width: 100%; height: 24px; background: var(--lavender); }
  .website {
    position: absolute; left: 120px; top: 871px; height: 55px; display: flex; align-items: center; gap: 10px;
    font-family: "Open Sans", sans-serif; font-style: italic; font-weight: 600; font-size: 21px;
  }
  .brand-block {
    position: absolute; left: 693px; top: 784px; width: 252px; height: 142px;
    background: var(--brand-bg); display: flex; align-items: center; justify-content: center;
    padding: 0 20px; text-align: center;
  }
  .brand-name { font-family: "Lexend", sans-serif; font-weight: 500; font-size: 21px; line-height: 28px; color: var(--white); }
</style>
</head>
<body>
<main class="flyer">
  <div class="frame">
    <h1 class="headline">JOIN OUR TEAM<br>TODAY!</h1>

    <ul class="benefits">
      <li style="top:297px">95% approval rating on all<br>submitted estimates.</li>
      <li style="top:391px">Guaranteed work volume.</li>
      <li style="top:454px">Material purchasing program to<br>help vendors with low capital or no<br>or bad credit.</li>
      <li style="top:581px">Weekly secure direct deposit with<br>net 30 payment terms.</li>
    </ul>

    <div class="divider"></div>

    <h2 class="requirements-title">REQUIREMENTS TO BECOME A<br>VENDOR</h2>
    <ul class="requirements">
      <li style="top:362px">Auto insurance</li>
      <li style="top:412px">Certificate of general liability insurance</li>
      <li style="top:463px">Workman’s Compensation or state issued<br>exemption letter</li>
      <li style="top:540px">Drive License or state issued ID card</li>
      <li style="top:590px">Coverage area</li>
      <li style="top:641px">Any speciality Licenses</li>
    </ul>

    <div class="contact-tab">CONTACT</div>
    <div class="phone">555-014-2290</div>

    <div class="footer-band"></div>
    <div class="footer-accent"></div>
    <div class="website">
      <svg width="24" height="24" viewBox="0 0 24 24" fill="none" stroke="#fff" stroke-width="1.6" aria-hidden="true">
        <circle cx="12" cy="12" r="10"/><ellipse cx="12" cy="12" rx="4.5" ry="10"/><line x1="2" y1="12" x2="22" y2="12"/>
      </svg>
      <span>www.brindleassetmanagement.com</span>
    </div>

    <div class="brand-block">
      <span class="brand-name">Brindle Asset Management</span>
    </div>
  </div>
</main>
</body>
</html>
```